Wholesale in Gold Jewellery & Gold Bullion

We are an established gold jewellery and gold bullion wholesaler selling these products to international clients. We already have a name and logo of our company, hence please view attached current card design. We need a completely new design to compliment our business and industry and the final design should be new and elegant.

Contact Information for Business Card

New card details must be same as per current card. Like logo, name, tel no. & etc.

Colors

Designer to choose colors to be used in the design.

```html
<!DOCTYPE html>
<html lang="en">
<head>
<meta charset="utf-8">
<title>Arvani &amp; Co Business Card</title>
<link href="https://fonts.googleapis.com/css2?family=Montserrat:wght@400;500&family=Libre+Baskerville:wght@700&display=swap" rel="stylesheet">
<style>
  :root {
    --page-bg: #d9d9d9;
    --card-bg: #f7f7f5;
    --gold: #c9951f;
    --gold-faint: #f1e8d6;
    --brown: #3a2518;
    --text-grey: #5a5a5a;
  }
  html, body {
    margin: 0;
    width: 1200px;
    height: 900px;
    overflow: hidden;
    background: var(--page-bg);
  }
  .card {
    position: absolute;
    left: 100px;
    top: 164px;
    width: 1000px;
    height: 572px;
    background: var(--card-bg);
    overflow: hidden;
    font-family: "Montserrat", Arial, sans-serif;
    box-shadow: 0 10px 30px rgba(0,0,0,0.18);
  }
  .backdrop-circle {
    position: absolute;
    left: 540px;
    top: -40px;
    width: 520px;
    height: 520px;
    border-radius: 50%;
    background: var(--gold-faint);
  }
  .brand {
    position: absolute;
    left: 70px;
    top: 130px;
    display: flex;
    align-items: center;
    gap: 30px;
  }
  .brand-dot {
    width: 86px;
    height: 86px;
    border-radius: 50%;
    background: var(--gold);
  }
  .brand-name {
    font-family: "Libre Baskerville", "Times New Roman", serif;
    font-weight: 700;
    font-size: 30px;
    color: var(--brown);
    letter-spacing: 0.5px;
  }
  .person {
    position: absolute;
    left: 110px;
    top: 300px;
  }
  .person-name {
    margin: 0;
    font-size: 40px;
    font-weight: 500;
    color: var(--gold);
  }
  .person-title {
    margin: 2px 0 0;
    font-size: 32px;
    font-weight: 400;
    color: var(--text-grey);
  }
  .address {
    position: absolute;
    left: 110px;
    top: 430px;
    margin: 0;
    font-size: 24px;
    line-height: 1.3;
    color: var(--text-grey);
    font-style: normal;
  }
  .contacts {
    position: absolute;
    right: 50px;
    top: 170px;
    margin: 0;
    padding: 0;
    list-style: none;
    text-align: right;
  }
  .contacts li {
    display: flex;
    justify-content: flex-end;
    align-items: center;
    gap: 18px;
    height: 40px;
    font-size: 24px;
    color: var(--text-grey);
  }
  .contacts .icon {
    width: 26px;
    height: 26px;
    flex: none;
  }
  .contacts .no-icon { width: 26px; }
</style>
</head>
<body>
  <div class="card">
    <div class="backdrop-circle"></div>

    <div class="brand">
      <div class="brand-dot"></div>
      <div class="brand-name">ARVANI &amp; CO PTE LTD</div>
    </div>

    <div class="person">
      <h1 class="person-name">Rohan Vellamuri</h1>
      <p class="person-title">Director</p>
    </div>

    <address class="address">12 Harlow Lane,<br>Singapore 218540</address>

    <ul class="contacts">
      <li>+65 9100 2458
        <svg class="icon" viewBox="0 0 24 24" aria-hidden="true"><rect x="6" y="2" width="12" height="20" rx="2" fill="none" stroke="#c9951f" stroke-width="2"/><circle cx="12" cy="18.5" r="1" fill="#c9951f"/></svg>
      </li>
      <li>+65 6810 3300
        <svg class="icon" viewBox="0 0 24 24" aria-hidden="true"><path d="M6 3l3 1 1 4-2 2c1 2.5 3 4.5 5.5 5.5l2-2 4 1 1 3-2 3C11 20 4 13 3 5z" fill="#c9951f"/></svg>
      </li>
      <li>+65 6402 7719
        <svg class="icon" viewBox="0 0 24 24" aria-hidden="true"><rect x="7" y="2" width="10" height="7" fill="none" stroke="#c9951f" stroke-width="2"/><rect x="3" y="10" width="18" height="11" rx="2" fill="#c9951f"/></svg>
      </li>
      <li>rohan@arvanico.com
        <svg class="icon" viewBox="0 0 24 24" aria-hidden="true"><rect x="2" y="5" width="20" height="14" fill="#c9951f"/><path d="M2 5l10 8 10-8" fill="none" stroke="#f7f7f5" stroke-width="1.6"/></svg>
      </li>
    </ul>
  </div>
</body>
</html>
```